Revamp Of Landing Page For an Automated AI Voice Agents Agency

here is my current landing page https://app.brightfernpromotionhub.biz/v2/preview/WXKRPmQ4hLzYBvNdTeGS?notrack=true

Please use all my current content and imagery of ai agents in your new design. Make it easy to ready, easy to navigate and easy to understand

I am looking for a SLEEK shiny polished looking website. I like Dark themed sites but am open to see light themed sites too so please dont be shy.

The site should have an Ai Voice Agent Theme about it. Maybe look and feel of futureistic but simple and not intimidating to the average person...

Here are a couple website designs I like for reference:
https://q7v.io/
https://ai-bots.marekholvin.com/
https://chatwelmo.com/ai-agents

Target Market(s)

b2b

Industry/Entity Type

AI Voice Agents

Coding

Coded - Design and coding required

Font styles to use
Other font styles liked:
• open

Requirements
Must have
• all elements and content and images used in existing design.
Nice to have
• open
Should not have
• open

```html
<!DOCTYPE html>
<html lang="en">
<head>
<meta charset="utf-8">
<title>Vantora Voice – AI Voice Agents</title>
<link rel="stylesheet" href="https://fonts.googleapis.com/css2?family=Outfit:wght@500;600;700&family=Montserrat:wght@400;500;600;700&display=swap">
<style>
:root{
  --ink:#141b26;
  --ink-2:#0f1622;
  --bar:#222b38;
  --white:#ffffff;
  --text:#1b1f29;
  --purple:#6a1bd6;
  --pink:#ff1f8f;
  --violet:#8a3bf2;
  --lav:#e5e8fb;
  --blue:#1c46e8;
  --green:#2da52b;
}
*{margin:0;padding:0;box-sizing:border-box}
html,body{width:1200px;height:5059px;overflow:hidden}
body{font-family:"Montserrat",sans-serif;color:var(--text);background:var(--white);position:relative}
h1,h2,.stars-box h3,.logo{font-family:"Outfit",sans-serif}
section,footer{position:absolute;left:0;width:1200px;overflow:hidden}
.abs{position:absolute}
.btn{position:absolute;display:flex;align-items:center;justify-content:center;height:32px;border-radius:16px;background:linear-gradient(90deg,var(--purple),var(--pink));color:#fff;font-size:12px;font-weight:500}
.note{font-size:11px;line-height:19px}
.note .link{color:var(--pink);text-decoration:underline}
.logo{color:#fff;font-weight:500;letter-spacing:2px;display:flex;align-items:center;gap:10px}
.logo .dot{width:14px;height:14px;border-radius:50%;background:var(--violet)}

/* hero */
.hero{top:0;height:636px;background:var(--ink)}
.hero h1{left:140px;top:160px;font-size:40px;line-height:48px;font-weight:600;background:linear-gradient(90deg,#6b2cf0,#e0169a);-webkit-background-clip:text;background-clip:text;color:transparent}
.hero .lead{left:140px;top:262px;width:360px;color:#fff;font-weight:600;font-size:13.5px;line-height:23px}
.hero .note{left:140px;top:404px;width:372px;color:#fff}
.hero-photo{left:650px;top:75px;width:470px;height:470px;border-radius:50%;border:2px solid #fff;padding:10px}
.hero-photo div{width:100%;height:100%;border-radius:50%;background:linear-gradient(160deg,#8fb4d0 0%,#3b7fb2 30%,#1c5485 60%,#0c2744 100%)}

/* workforce */
.workforce{top:636px;height:1087px;background:#fff}
.workforce .ring{left:-60px;top:15px;width:500px;height:500px;border-radius:50%;border:1px solid #eceef2}
.workforce h2{left:140px;top:100px;font-size:31px;line-height:38px;font-weight:600;color:#111}
.workforce .note{left:140px;top:325px;width:250px;color:#333}
.card{position:absolute;width:288px;background:#fff;border-radius:8px;box-shadow:0 4px 14px rgba(0,0,0,.12);padding:8px;text-align:center}
.card .shot{height:178px;border-radius:4px}
.card .badge{width:60px;height:60px;border-radius:50%;margin:-30px auto 0;border:3px solid #fff;position:relative;display:flex;align-items:center;justify-content:center}
.card .badge svg{width:30px;height:30px}
.card h3{font-size:14.5px;font-weight:500;margin:14px 0 10px}
.card p{font-size:11px;line-height:18px;color:#333;padding:0 18px}
.card p b{font-weight:600;color:#111}

/* wish */
.wish{top:1723px;height:395px;background:radial-gradient(ellipse at 50% 110%,#2b4fc6 0%,#13286e 45%,#0c1444 100%);text-align:center;color:#fff}
.wish .kicker{top:92px;width:100%;font-size:14px;color:#ff3a1a;font-weight:500}
.wish h2{top:118px;width:100%;font-size:31px;font-weight:600}
.wish .body{top:183px;left:250px;width:700px;font-size:14px;line-height:23px;font-weight:600}

/* never sick */
.sick{top:2118px;height:434px;background:#f4f5f8;text-align:center}
.sick h2{top:98px;width:100%;font-size:31px;font-weight:600;color:#111}
.perk{position:absolute;top:168px;width:220px}
.perk .ic{width:88px;height:88px;margin:0 auto;border-radius:50%;border:2px dashed;display:flex;align-items:center;justify-content:center}
.perk .ic span{width:70px;height:70px;border-radius:50%;background:#111;display:flex;align-items:center;justify-content:center}
.perk .ic svg{width:38px;height:38px}
.perk h3{font-size:14px;font-weight:500;margin-top:22px}
.perk p{font-size:11px;line-height:18px;color:#444;margin-top:10px}

/* hired */
.hired{top:2552px;height:538px;background:radial-gradient(ellipse at 0% 0%,#5b1a9c 0%,#1c1a44 30%,var(--ink-2) 60%)}
.hired h2{left:142px;top:88px;font-size:31px;line-height:39px;font-weight:600;color:#fff}
.hired .kicker{left:142px;top:190px;color:#ff9a1a;font-size:13px;font-weight:600}
.hired .lead{left:142px;top:214px;color:#fff;font-size:19px;line-height:28px;font-weight:500}
.hired .note{left:142px;top:358px;width:372px;color:#fff}
.bolt{left:760px;top:40px;width:320px;height:498px;border-radius:12px;background:linear-gradient(200deg,#1a1440 0%,#5a1d8c 35%,#e0268a 60%,#3a1660 85%,#141a2c 100%)}

/* promise */
.promise{top:3090px;height:530px;background:linear-gradient(180deg,#f6f7fb,#fff 60%,#e9f2fb)}
.stars-box{left:140px;top:90px;width:290px;height:350px;background:var(--lav);border-radius:10px;text-align:center;padding-top:38px}
.stars-box h3{font-size:24px;line-height:38px;font-weight:600;color:#111}
.stars{display:flex;justify-content:center;gap:6px;margin-top:4px}
.stars svg{width:28px;height:28px}
.promise h2{left:455px;top:130px;width:603px;text-align:center;font-size:31px;font-weight:600;color:#111}
.pcard{position:absolute;top:182px;width:290px;height:255px;background:#fff;border-radius:8px;box-shadow:0 4px 14px rgba(0,0,0,.1);text-align:center;padding-top:42px}
.pcard .ic{width:76px;height:76px;border-radius:50%;margin:0 auto;display:flex;align-items:center;justify-content:center}
.pcard .ic svg{width:38px;height:38px}
.pcard h3{font-size:14px;font-weight:500;line-height:20px;margin-top:24px}
.pcard p{font-size:11px;line-height:18px;color:#444;margin-top:6px}

/* faq */
.faq{top:3620px;height:625px;background:var(--ink)}
.robot{left:140px;top:80px;width:430px;height:470px;border-radius:14px;background:linear-gradient(120deg,#5b20b0 0%,#7b34d6 40%,#9aa2b4 62%,#d7dbe3 80%,#5c6474 100%)}
.faq h2{left:650px;top:88px;font-size:31px;font-weight:600;color:#fff}
.qa{position:absolute;left:652px;width:408px}
.qa .q{height:40px;background:var(--bar);border-radius:3px;display:flex;align-items:center;gap:14px;padding-left:12px;color:#fff;font-size:14px;font-weight:500}
.qa .q i{width:22px;height:22px;border-radius:50%;border:3px solid var(--violet);display:block}
.qa .a{color:#d8dbe2;font-size:11.5px;line-height:21px;padding:12px 36px 0 52px}

/* cta */
.cta{top:4245px;height:432px;background:linear-gradient(180deg,#eef6fc,#fff 40%,#eef4fb);text-align:center}
.cta h2{top:88px;width:100%;font-size:31px;line-height:39px;font-weight:600;color:#111}
.cta .btn{left:498px;top:218px;width:204px}
.cta .note{top:282px;left:310px;width:580px;color:#333}

/* footer */
.site-footer{top:4677px;height:382px;background:var(--ink);color:#fff}
.site-footer .logo{top:105px;width:100%;justify-content:center;font-size:32px}
.site-footer .rule{left:140px;top:170px;width:920px;height:1px;background:#3a4350}
.site-footer .small{font-size:10.5px}
.site-footer .copy{left:142px;top:190px}
.site-footer .legal{right:140px;top:190px}
.site-footer .terms{left:140px;top:224px;width:920px;height:34px;border-radius:17px;background:linear-gradient(90deg,var(--purple),var(--pink));display:flex;align-items:center;padding-left:20px;font-size:11px}
.site-footer .ask{top:288px;width:100%;text-align:center}
.site-footer .important{top:326px;width:100%;text-align:center;line-height:18px}
</style>
</head>
<body>

<section class="hero">
  <div class="abs logo" style="left:140px;top:22px;font-size:22px"><span class="dot"></span>VANTORA</div>
  <h1 class="abs">AI VOICE AGENTS<br>THAT ANSWER CALLS,</h1>
  <p class="abs lead">Book Appts, Send Emails, Text Messages, Follow Up Reminders, Transfer Calls &amp; More For You 24 Hours 7 Days A Week!</p>
  <div class="btn" style="left:140px;top:358px;width:204px">Get An Instant Free Demo</div>
  <p class="abs note">We Will Create An Ai Agent Customized For Your Business At No Cost. Simply <span class="link">Click The Button</span> Above And Your Very Own Ai Agent Will Be Calling You In Just A Couple Minutes. Experience The Magic And Get Ready To Be Very Impressed!</p>
  <div class="abs hero-photo"><div role="img" aria-label="Man with headset working at a laptop in a blue-lit office"></div></div>
</section>

<section class="workforce">
  <div class="abs ring"></div>
  <h2 class="abs">MEET YOUR<br>NEW AI-<br>POWERED<br>WORKFORCE</h2>
  <div class="btn" style="left:140px;top:272px;width:204px">Get An Instant Free Demo</div>
  <p class="abs note">We Will Create An Ai Agent Customized For Your Business At No Cost. Simply <span class="link">Click The Button</span> Above And Your Very Own Ai Agent Will Be Calling You In Just A Couple Minutes. Experience The Magic And Get Ready To Be Very Impressed!</p>

  <div class="card" style="left:452px;top:90px;height:440px">
    <div class="shot" role="img" aria-label="AI sales agent with headset at a desk by city windows" style="background:linear-gradient(135deg,#c7cdd6,#6d7784)"></div>
    <div class="badge" style="background:#5a1ec0"><svg viewBox="0 0 24 24" fill="none" stroke="#fff" stroke-width="2"><rect x="4" y="5" width="16" height="11" rx="2"/><path d="M9 20h6M12 16v4"/></svg></div>
    <h3>Ai Sales Agent</h3>
    <p>Brian will take your inbound sales calls. Will give all detailed information to the customer, answer questions in a normal conversational tone and can book sales appointments or transfer hot prospects to a human to close the sale.</p>
  </div>
  <div class="card" style="left:768px;top:90px;height:440px">
    <div class="shot" role="img" aria-label="AI receptionist with headset in a bright office" style="background:linear-gradient(135deg,#9ec6d8,#3b6f8a)"></div>
    <div class="badge" style="background:#e4177f"><svg viewBox="0 0 24 24" fill="none" stroke="#fff" stroke-width="2"><path d="M5 4h4l2 5-2.5 1.5a11 11 0 005 5L15 13l5 2v4a2 2 0 01-2 2A16 16 0 013 6a2 2 0 012-2"/></svg></div>
    <h3>Ai Receptionist</h3>
    <p><b>Takes Overflow and After Hours Calls or Can Take Calls 24/7 &amp; Transfer To Appropriate Dept.</b><br>Cody handles all your calls 24/7. You can also set him to only take overflow calls and after hours. He can send eails and sms messages and even book appointments over the call</p>
  </div>
  <div class="card" style="left:140px;top:555px;height:385px">
    <div class="shot" role="img" aria-label="AI appointment setter with headset in an office" style="background:linear-gradient(135deg,#8fb0c4,#2c4a5e)"></div>
    <div class="badge" style="background:#1f7a36"><svg viewBox="0 0 24 24" fill="none" stroke="#fff" stroke-width="2"><rect x="4" y="5" width="16" height="15" rx="2"/><path d="M4 10h16M9 3v4M15 3v4"/></svg></div>
    <h3>Ai Appointment Setter</h3>
    <p><b>Book Appts &amp; Reservations On Auto Pilot</b><br>Bobby offers business advice, helps brainstorm ideas, and provides insights on growth tactics to support your entrepreneurial journey.</p>
  </div>
  <div class="card" style="left:452px;top:555px;height:385px">
    <div class="shot" role="img" aria-label="AI lead qualifier at a computer in a dark blue office" style="background:linear-gradient(135deg,#2f6a9a,#0d2440)"></div>
    <div class="badge" style="background:#1c46e8"><svg viewBox="0 0 24 24" fill="none" stroke="#fff" stroke-width="2"><circle cx="11" cy="11" r="6"/><path d="M16 16l4 4"/></svg></div>
    <h3>Ai Lead Qualifier</h3>
    <p><b>Conversate With Prospects To Qualify Before Handing Over To Sales Team</b><br>All of our ai agents gather information and qualify leads. If they are interested in the services on the call then our ai agents will assist them with booking an appointment with our sales team over the call.</p>
  </div>
  <div class="card" style="left:768px;top:555px;height:385px">
    <div class="shot" role="img" aria-label="AI follow-up assistant with headset in a lit office" style="background:linear-gradient(135deg,#7d98b5,#26384f)"></div>
    <div class="badge" style="background:#f28a0f"><svg viewBox="0 0 24 24" fill="none" stroke="#fff" stroke-width="2"><path d="M6 16V11a6 6 0 0112 0v5l2 2H4z"/><path d="M10 21h4"/></svg></div>
    <h3>Ai Follow Up Reminders</h3>
    <p><b>Calls, Sends SMS &amp; Email Reminders</b><br>Sam handles all the follow up calls, appt reminders and sends out the email and sms reminders too.</p>
  </div>
</section>

<section class="wish">
  <p class="abs kicker">INSTALL THE POWER OF AI FOR YOUR BUSINESS</p>
  <h2 class="abs">YOUR WISH IS THEIR COMMAND</h2>
  <p class="abs body">Your New Ai Agents Will Never Call In Sick And Will Never Complain!<br><span style="display:block;height:8px"></span>With your new team of AI Agents, handling inbound calls, sending emails and sms messages, booking appointments and handling customer service inquiries is going to save you a ton of time and money.</p>
</section>

<section class="sick">
  <h2 class="abs">AN EMPLOYEE THAT NEVER GETS SICK!</h2>
  <div class="perk" style="left:237px"><div class="ic" style="border-color:#2da52b"><span><svg viewBox="0 0 24 24" fill="none" stroke="#fff" stroke-width="1.6"><rect x="6" y="6" width="12" height="12" rx="2"/><path d="M9 2v4M15 2v4M9 18v4M15 18v4M2 9h4M2 15h4M18 9h4M18 15h4"/><path d="M13 8.5l-3 4h4l-3 3.5"/></svg></span></div><h3>TRAINED IN SECONDS</h3><p>Learns Your Entire Website<br>In Seconds</p></div>
  <div class="perk" style="left:490px"><div class="ic" style="border-color:#d93a9a"><span><svg viewBox="0 0 24 24" fill="none" stroke="#fff" stroke-width="1.6"><circle cx="12" cy="12" r="9"/><ellipse cx="12" cy="12" rx="4" ry="9"/><path d="M3 12h18M5 7h14M5 17h14"/></svg></span></div><h3>WORLDWIDE</h3><p>Works Anywhere In<br>The Globe</p></div>
  <div class="perk" style="left:743px"><div class="ic" style="border-color:#f0a020"><span><svg viewBox="0 0 24 24" fill="none" stroke="#fff" stroke-width="1.6"><circle cx="12" cy="8" r="4"/><path d="M4 21a8 8 0 0116 0"/></svg></span></div><h3>USER-FRIENDLY</h3><p>Your Ai Agents Sound As If<br>They're Real Humans</p></div>
</section>

<section class="hired">
  <h2 class="abs">OUR AI AGENTS<br>OUR READY TO BE HIRED</h2>
  <p class="abs kicker">LIGHTNING-FAST RESPONSES</p>
  <p class="abs lead">Instant answers, no coffee, bathroom<br>or lunch breaks needed</p>
  <div class="btn" style="left:142px;top:298px;width:204px">Get An Instant Free Demo</div>
  <p class="abs note">We Will Create An Ai Agent Customized For Your Business At No Cost. Simply <span class="link">Click The Button</span> Above And Your Very Own Ai Agent Will Be Calling You In Just A Couple Minutes. Experience The Magic And Get Ready To Be Very Impressed!</p>
  <div class="abs bolt" role="img" aria-label="Glowing pink lightning bolt above lightning responses lettering"></div>
</section>

<section class="promise">
  <div class="abs stars-box">
    <h3>AFTER OUR<br>CUSTOMERS HAVE<br>A CONVERSATION<br>WITH THEIR NEW AI<br>VOICE AGENT THEY<br>GIVE US 5 STARS!</h3>
    <div class="stars">
      <svg viewBox="0 0 24 24"><path fill="#f08a12" d="M12 2l3 7h7l-5.5 4.5 2 7.5-6.5-4.5L5.5 21l2-7.5L2 9h7z"/></svg>
      <svg viewBox="0 0 24 24"><path fill="#f08a12" d="M12 2l3 7h7l-5.5 4.5 2 7.5-6.5-4.5L5.5 21l2-7.5L2 9h7z"/></svg>
      <svg viewBox="0 0 24 24"><path fill="#f08a12" d="M12 2l3 7h7l-5.5 4.5 2 7.5-6.5-4.5L5.5 21l2-7.5L2 9h7z"/></svg>
      <svg viewBox="0 0 24 24"><path fill="#f08a12" d="M12 2l3 7h7l-5.5 4.5 2 7.5-6.5-4.5L5.5 21l2-7.5L2 9h7z"/></svg>
      <svg viewBox="0 0 24 24"><path fill="#f08a12" d="M12 2l3 7h7l-5.5 4.5 2 7.5-6.5-4.5L5.5 21l2-7.5L2 9h7z"/></svg>
    </div>
  </div>
  <h2 class="abs">OUR PROMISE TO YOU:</h2>
  <div class="pcard" style="left:455px">
    <div class="ic" style="background:var(--green)"><svg viewBox="0 0 24 24" fill="none" stroke="#fff" stroke-width="2"><rect x="4" y="5" width="16" height="15" rx="2"/><path d="M4 10h16M9 3v4M15 3v4"/></svg></div>
    <h3>14-DAY MONEY-BACK<br>GUARANTEE*</h3>
  </div>
  <div class="pcard" style="left:770px">
    <div class="ic" style="background:var(--blue)"><svg viewBox="0 0 24 24" fill="none" stroke="#fff" stroke-width="2"><circle cx="12" cy="12" r="8"/><path d="M12 8v4l3 2"/></svg></div>
    <h3>24/7 CUSTOMER<br>SUPPORT</h3>
    <p>Often praised for our friendly<br>&amp; helpful support team</p>
  </div>
</section>

<section class="faq">
  <div class="abs robot" role="img" aria-label="Silver robot leaning on a large purple question mark"></div>
  <h2 class="abs">DO YOU HAVE QUESTIONS?</h2>
  <div class="qa" style="top:150px"><div class="q"><i></i>What exactly are the AI Voice Agents?</div><p class="a">AI Voice Agents are specialized human sounding bots, having smart and masterful conversations and each is expertly trained in seconds for a specific business function.</p></div>
  <div class="qa" style="top:306px"><div class="q"><i></i>How will these AI Voice Agents benefit</div><p class="a">Ai Voice Agents Answer Calls, Book Appts, Send Emails, Text Messages, Follow Up Reminders &amp; More For You 24/7!</p></div>
  <div class="qa" style="top:442px"><div class="q"><i></i>Are they easy to use?</div><p class="a">We provide a done for you service. We create your AI Voice Agent and launch it within days!</p></div>
</section>

<section class="cta">
  <h2 class="abs">THESE AI AGENTS CAN HELP<br>YOUR BUSINESS TREMENDOUSLY.<br>IMAGINE THE POSSIBILITIES</h2>
  <div class="btn">Get An Instant Free Demo</div>
  <p class="abs note">We Will Create An Ai Agent Customized For Your Business At No Cost. Simply <span class="link">Click The Button</span> Above And Your Very Own Ai Agent Will Be Calling You In Just A Couple Minutes. Experience The Magic And Get Ready To Be Very Impressed!</p>
</section>

<footer class="site-footer">
  <div class="abs logo"><span class="dot" style="width:20px;height:20px"></span>VANTORA</div>
  <div class="abs rule"></div>
  <p class="abs small copy">© 2025 Vantora Voice. All rights reserved.</p>
  <p class="abs small legal">Disclaimer: Privacy | Terms &amp; Conditions | Earnings &amp; Products Disclaimer</p>
  <div class="abs terms">*14-Day Money Back Guarantee Terms: If you use the ai agents and you're not happy. Then you can contact us in the first 14 days for a full refund.</div>
  <p class="abs small ask">Do you have questions about ( ) Please email ( )</p>
  <p class="abs small important">IMPORTANT: This site is not a part of the Linkora website or Linkora Inc. Additionally,<br>this site is NOT endorsed by Linkora in any way. LINKORA is a trademark of LINKORA, Inc.</p>
</footer>

</body>
</html>
```